App-Design für Vergleichsportal für Reparaturen
Zielgruppe
Flickwerkzentrale ist das Vergleichsportal für Reparaturen in deiner Nähe. Egal ob du eine Werkstatt für dein Smartphone, Tablet, Laptop, Computer, Smartwatch oder Spielkonsole suchst. Mit uns findest du deine passende Reparaturwerkstat in deiner Nähe mit dem besten Preis für dich. Du kannst dich direkt über unser Portal deinen Reparaturauftrag erhalten und wirst durch unser Sicher Kaufen Käuferschutz und unser VORMANT Treuhandschutz abgesichert.
Aufgabenstellung
Unter Flickwerkzentrale.de kann das aktuelle Design angeschaut werden. Die Farbe sollten übernommen werden.
Über die Startseite kann der Kunde sein Gerät, Service sowie seine Adresse eingeben. Auf der Vergleichsseite bekommt der Kunde die Übersicht welche Reparaturwerkstätten es gibt, zu welche Preisen die ausgewählte Dienstleistung angeboten wird. Wenn der Kunde auf den Button 'Jetzt Online Bestpreis buchen' drückt, dann kommt der Kunde in den Warenkorb. Im Warenkorb können noch weitere Dienstleistungen und Produkte dazugebucht werden. Und anschließend kommt der Kunde in die Kasse und kann der Bestellvorgang beenden. Die Benutzerführung sollte einfach sein. Im Fokus steht die Vergleichsseite. Dort sollte der Kunde ca. 4 Werkstätten auf einen Blick sehen können. Könnte ausschauen wie bei Tarifblick in der Kategorie Mobilfunk.
Die Vergleichseite sollte auf jeden Fall folgende Elemente enthalten:
- Entfernung zur Werkstatt in Meter bzw. Kilometer
- Logo der Werkstatt
- Name der Werkstatt
- Bewertungssterne der Werkstatt
- Reparaturzeit und Ersatzeilverfügbarkeit
- Reparaturpreis (Platz sollte auch bei Auswahl von 2 Dienstleistungen vorhanden sein)
- Rabattanzeige
- Qualitätssiegel (noch nicht vorhanden)
- Anzeige von Verknappung (z. B. noch 3 Termin frei)
- Qualitätsmerkmale (z. B. 12 Monate Garantie)
Die Merkmale Öffnungszeiten, Adresse, Kostenpflichtige Zusatzleistungen können aus Platzgründen in den Warenkorbseite wandern außer es gibt eine schöne und einfache Lösung.
In der Warenkorbseite kann dazu auch die Tarifblick Seite dienen.
Bei allen sollte auf die Benutzerfreundlichkeit geachtet werden.
Bei offenen Frage stehe ich zur Verfügung und freue mich auf viele Designs.
Vielen DANK im Voraus!

```html
<!DOCTYPE html>
<html lang="de">
<head>
<meta charset="utf-8">
<title>Flickwerkzentrale – App Screens</title>
<link href="https://fonts.googleapis.com/css2?family=Roboto:wght@400;500;700&display=swap" rel="stylesheet">
<style>
:root{
  --page:#f6f6f6;
  --grey:#ececec;
  --white:#ffffff;
  --green:#8dc63f;
  --navy:#1f4357;
  --text:#222222;
  --muted:#8a8a8a;
  --line:#e4e4e4;
  --disabled:#a3b3bc;
  --link:#7f95c8;
}
*{box-sizing:border-box;margin:0;padding:0}
html,body{width:1200px;height:1000px;overflow:hidden;background:var(--page);font-family:"Roboto",Helvetica,Arial,sans-serif;color:var(--text)}
.board{position:absolute;left:0;top:0;width:1434px;height:1195px;transform:scale(0.8368);transform-origin:0 0}
.screen{position:absolute;width:277px;height:494px;background:var(--grey);box-shadow:0 1px 4px rgba(0,0,0,.18);overflow:hidden}
.abs{position:absolute}
.statusbar{position:absolute;left:0;top:0;width:100%;height:16px;background:var(--white);font-size:8px;display:flex;align-items:center;justify-content:space-between;padding:0 5px}
.statusbar .clock{position:absolute;left:0;right:0;text-align:center}
.batt{display:inline-block;width:16px;height:7px;background:#111;vertical-align:middle;margin-left:2px;border-radius:1px}
.appbar{position:absolute;top:16px;left:0;width:100%;height:46px;background:var(--white)}
.brand{position:absolute;left:0;right:0;top:16px;text-align:center;color:var(--green);font-size:10px;font-weight:500}
.brand .dot{display:inline-block;width:7px;height:7px;border-radius:50%;background:var(--navy);margin-right:3px;vertical-align:-1px}
.back{position:absolute;left:16px;top:15px}
.basket{position:absolute;right:18px;top:13px}
.label{position:absolute;left:0;width:100%;text-align:center;font-size:7px;font-weight:500;color:#333}
.row{position:absolute;left:0;width:100%;height:33px;background:var(--white);font-size:9.5px;display:flex;align-items:center;padding:0 32px;border-bottom:1px solid var(--line)}
.row.placeholder{color:var(--muted)}
.row .chev{margin-left:auto;font-size:11px;color:#777}
.btn{position:absolute;left:17px;width:239px;height:35px;background:var(--navy);color:var(--white);font-size:10px;font-weight:700;letter-spacing:.4px;display:flex;align-items:center;justify-content:center}
.btn.disabled{background:var(--disabled)}
.card{position:absolute;top:103px;height:77px;background:var(--white);font-size:9px;text-align:center}
.card.active{background:var(--green);color:var(--white)}
.card span{position:absolute;left:0;right:0;bottom:8px}
.card svg{position:absolute;left:50%;top:12px;transform:translateX(-50%)}
.dots{position:absolute;left:0;width:100%;text-align:center;font-size:0}
.dots i{display:inline-block;width:3px;height:3px;border-radius:50%;background:#c4c4c4;margin:0 1.5px}
.dots i.on{background:var(--green)}
.loc{font-size:8.5px}
.loc b{display:inline-block;width:34px;font-size:7.5px;font-weight:700}
.loc b small{font-weight:400;font-size:5px}
.line-item{position:absolute;left:0;width:100%;height:33px;background:var(--white);border-bottom:1px solid var(--line);font-size:9.5px;display:flex;align-items:center;padding:0 32px 0 20px}
.line-item .x{color:#aaa;margin-right:10px;font-size:9px}
.line-item .old{margin-left:auto;font-size:5.5px;color:var(--link);margin-right:4px}
.line-item .price{font-weight:700;font-size:9.5px}
.line-item .price.solo{margin-left:auto}
.total{position:absolute;left:0;width:100%;height:23px;background:var(--green);color:var(--white);font-size:8px;font-weight:700;display:flex;align-items:center;justify-content:space-between;padding:0 30px 0 35px}
.shop{position:absolute;left:23px;top:88px;width:231px;height:249px;background:var(--white);border:2px solid var(--green)}
.shop-under{position:absolute;left:40px;top:77px;width:197px;height:12px;background:#dcdcdc}
.slot{position:absolute;height:28px;border:1px solid #d8d8d8;background:var(--white);font-size:10px;color:#555;display:flex;align-items:center;justify-content:center}
.slot.on{background:var(--green);border-color:var(--green);color:var(--white)}
.title{position:absolute;left:0;width:100%;text-align:center;color:var(--navy);font-size:21px;font-weight:700}
.suggest{position:absolute;left:0;width:100%;height:33px;background:var(--white);border-bottom:1px solid var(--line);font-size:9.5px;display:flex;align-items:center;padding:0 25px 0 32px}
.suggest .ic{width:14px;font-size:8px}
.suggest .info{margin-left:auto;width:8px;height:8px;border-radius:50%;background:#cfcfcf;color:#fff;font-size:6px;text-align:center;line-height:8px}
.center-text{position:absolute;left:0;width:100%;text-align:center;font-size:9px;line-height:14px}
.paybox{position:absolute;top:284px;height:21px;background:var(--white);border:1px solid #ddd;font-size:9px;font-weight:700;color:var(--navy);display:flex;align-items:center;justify-content:center}
</style>
</head>
<body>
<div class="board">

<!-- Screen: Start -->
<section class="screen" style="left:80px;top:77px;background:var(--white)">
  <div class="statusbar"><span>●●●●● Netz</span><span class="clock">9:41 AM</span><span>100%<i class="batt"></i></span></div>
  <div class="abs" style="left:0;right:0;top:162px;text-align:center;color:var(--green);font-size:26px;font-weight:500"><span style="display:inline-block;width:18px;height:18px;border-radius:50%;background:var(--navy);vertical-align:-1px;margin-right:6px"></span>Flickwerkzentrale</div>
  <div class="abs" style="left:0;right:0;top:386px;text-align:center;font-size:11px;font-weight:700;line-height:16px">DAS VERGLEICHSPORTAL FÜR<br>REPARATUREN IN DEINER NÄHE</div>
  <div class="abs" style="left:0;bottom:0;width:100%;height:14px;background:var(--grey);font-size:4.5px;color:#999;text-align:center;line-height:14px">Datenschutz</div>
</section>

<!-- Screen: Kategorie -->
<section class="screen" style="left:398px;top:77px">
  <div class="statusbar"><span>●●●●● Netz</span><span class="clock">9:41 AM</span><span>100%<i class="batt"></i></span></div>
  <div class="appbar">
    <div class="brand"><i class="dot"></i>Flickwerkzentrale</div>
    <svg class="basket" width="18" height="16" viewBox="0 0 18 16"><path d="M2 6h14l-2 8H4z M5 6l4-5 4 5" fill="none" stroke="#333" stroke-width="1.3"/></svg>
  </div>
  <div class="label" style="top:84px">Bitte wählen Sie die Reparaturkategorie</div>
  <div class="card" style="left:-88px;width:101px"><svg width="14" height="32" viewBox="0 0 14 32" style="left:auto;right:0;transform:none"><rect x="1" y="1" width="12" height="30" fill="none" stroke="#111" stroke-width="2"/></svg></div>
  <div class="card active" style="left:32px;width:101px"><svg width="28" height="36" viewBox="0 0 28 36"><rect x="2" y="2" width="24" height="32" rx="3" fill="none" stroke="#fff" stroke-width="2.5"/></svg><span>Tablet</span></div>
  <div class="card" style="left:139px;width:100px"><svg width="46" height="32" viewBox="0 0 46 32"><rect x="4" y="4" width="38" height="22" fill="none" stroke="#111" stroke-width="1.8"/><path d="M0 29h46" stroke="#111" stroke-width="1.8"/></svg><span>Laptop</span></div>
  <div class="card" style="left:245px;width:100px"></div>
  <div class="dots" style="top:190px"><i></i><i class="on"></i><i></i><i></i><i></i></div>
  <div class="row placeholder" style="top:208px">Hersteller wählen<span class="chev">›</span></div>
  <div class="row placeholder" style="top:250px">Dienstleistung wählen<span class="chev">›</span></div>
  <div class="label" style="top:324px">Geben Sie Ihre Agresse ein</div>
  <div class="row placeholder" style="top:341px">Strasse</div>
  <div class="row placeholder" style="top:383px">Hausnummer</div>
  <div class="btn" style="top:436px">LOS</div>
</section>

<!-- Screen: Gerät -->
<section class="screen" style="left:718px;top:77px">
  <div class="statusbar"><span>●●●●● Netz</span><span class="clock">9:41 AM</span><span>100%<i class="batt"></i></span></div>
  <div class="appbar">
    <svg class="back" width="10" height="16" viewBox="0 0 10 16"><path d="M8 1L2 8l6 7" fill="none" stroke="#222" stroke-width="1.8"/></svg>
    <div class="brand"><i class="dot"></i>Flickwerkzentrale</div>
    <svg class="basket" width="20" height="17" viewBox="0 0 20 17"><path d="M2 7h14l-2 8H4z M5 7l4-5 4 5" fill="none" stroke="#222" stroke-width="1.5"/><text x="15" y="5" font-size="7" font-family="Roboto,sans-serif">3</text></svg>
  </div>
  <div class="label" style="top:84px">Gerät wählen</div>
  <div class="card" style="left:-72px;width:101px"></div>
  <div class="card active" style="left:32px;width:102px"><svg width="28" height="36" viewBox="0 0 28 36"><rect x="2" y="2" width="24" height="32" rx="3" fill="none" stroke="#fff" stroke-width="2.5"/></svg><span>Tab Pro 2 12,9</span></div>
  <div class="card" style="left:140px;width:100px"><svg width="28" height="38" viewBox="0 0 28 38"><rect x="2" y="2" width="24" height="34" rx="3" fill="none" stroke="#111" stroke-width="2.5"/></svg><span>Tab Pro 10,5</span></div>
  <div class="card" style="left:247px;width:100px"></div>
  <div class="dots" style="top:187px"><i></i><i class="on"></i><i></i><i></i><i></i></div>
  <div class="row" style="top:207px">Dienstleistung wählen<span class="chev">›</span></div>
  <div class="label" style="top:261px">Standorte in der Nähe</div>
  <div class="row loc" style="top:281px"><b>2 <small>km.</small></b>Lindenallee 14, Berlin</div>
  <div class="row loc" style="top:314px"><b>13 <small>km.</small></b>Ahornweg 6 89350 ...</div>
  <div class="row loc" style="top:348px"><b>100 <small>m.</small></b>Lindenallee 14,10407 Berlin</div>
  <div class="row loc" style="top:381px"><b>100 <small>m.</small></b>Ahornweg 6 89350 ...</div>
  <div class="btn" style="top:436px">VERGLEICHEN</div>
</section>

<!-- Screen: Vergleich -->
<section class="screen" style="left:1047px;top:77px">
  <div class="statusbar"><span>●●●●● Netz</span><span class="clock">9:41 AM</span><span>100%<i class="batt"></i></span></div>
  <div class="appbar">
    <svg class="back" width="10" height="16" viewBox="0 0 10 16"><path d="M8 1L2 8l6 7" fill="none" stroke="#222" stroke-width="1.8"/></svg>
    <div class="brand"><i class="dot"></i>Flickwerkzentrale</div>
    <svg class="basket" width="20" height="17" viewBox="0 0 20 17"><path d="M2 7h14l-2 8H4z M5 7l4-5 4 5" fill="none" stroke="#222" stroke-width="1.5"/><text x="15" y="5" font-size="7" font-family="Roboto,sans-serif">3</text></svg>
  </div>
  <div class="shop-under"></div>
  <div class="shop">
    <div class="abs" style="left:37px;top:29px;font-size:6px;font-weight:700;color:var(--green)">Fonwerk.de</div>
    <div class="abs" style="right:17px;top:29px;font-size:5.5px;color:var(--link);text-decoration:underline">Show on map</div>
    <div class="abs" style="left:37px;top:50px;font-size:14px;font-weight:700;line-height:18px">Fonwerk<br>Sicher Kaufen</div>
    <div class="abs" style="left:37px;top:100px;font-size:8px;line-height:14px">Ahornweg 6<br>89350 Talheim</div>
    <div class="abs" style="left:37px;top:137px;font-size:7.5px;line-height:15px">✆ 07123 - 4560 111<br>✆ 07123 - 4560 125</div>
    <div class="abs" style="left:39px;top:185px;font-size:24px;font-weight:700">150 <span style="font-size:15px;font-weight:500">m.</span></div>
    <div class="abs" style="left:39px;top:213px;font-size:11px;color:var(--green);letter-spacing:1px">★★★★<span style="color:#d0d0d0">★</span></div>
    <svg class="abs" style="left:150px;top:184px" width="26" height="26" viewBox="0 0 26 26"><rect x="2" y="4" width="22" height="20" fill="none" stroke="#111" stroke-width="1.8"/><path d="M2 9h22M7 1v5M19 1v5" stroke="#111" stroke-width="1.8"/><text x="13" y="21" font-size="10" font-weight="700" text-anchor="middle" font-family="Roboto,sans-serif">19</text></svg>
    <div class="abs" style="left:135px;top:215px;font-size:5.5px;color:var(--link)">noch <b style="font-size:8px;color:#222">3</b> Termin frei</div>
  </div>
  <div class="dots" style="top:344px"><i></i><i class="on"></i><i></i><i></i><i></i></div>
  <div class="line-item" style="top:358px"><span class="x">✕</span>Bluetooth Antenne<span class="old">200€ -50%</span><span class="price">100 €</span></div>
  <div class="line-item" style="top:391px"><span class="x">✕</span>SIM Lesemodul<span class="price solo">100 €</span></div>
  <div class="btn" style="top:436px">JETZT ONLINE BESTPREIS BUCHEN</div>
</section>

<!-- Screen: Termine -->
<section class="screen" style="left:398px;top:618px">
  <div class="statusbar"><span>●●●●● Netz</span><span class="clock">9:41 AM</span><span>100%<i class="batt"></i></span></div>
  <div class="appbar">
    <svg class="back" width="10" height="16" viewBox="0 0 10 16"><path d="M8 1L2 8l6 7" fill="none" stroke="#222" stroke-width="1.8"/></svg>
    <div class="brand"><i class="dot"></i>Flickwerkzentrale</div>
    <svg class="basket" width="20" height="17" viewBox="0 0 20 17"><path d="M2 7h14l-2 8H4z M5 7l4-5 4 5" fill="none" stroke="#222" stroke-width="1.5"/><text x="15" y="5" font-size="7" font-family="Roboto,sans-serif">3</text></svg>
  </div>
  <div class="abs" style="left:13px;top:84px;width:250px;height:324px;background:var(--white);border:2px solid var(--green)">
    <div class="abs" style="left:18px;top:15px;font-size:10px;font-weight:700">Nächste Termine</div>
    <div class="abs" style="right:16px;top:10px;font-size:14px;color:#aaa">✕</div>
    <div class="abs" style="left:18px;top:46px;font-size:9px">AUG 17</div>
    <div class="slot on" style="left:18px;top:63px;width:57px">11 AM</div>
    <div class="slot" style="left:89px;top:63px;width:59px">1 PM</div>
    <div class="slot" style="left:160px;top:63px;width:59px">3 PM</div>
    <div class="slot" style="left:18px;top:104px;width:58px">4 PM</div>
    <div class="slot" style="left:89px;top:104px;width:59px">11 AM</div>
    <div class="abs" style="left:18px;top:153px;font-size:9px">AUG 19</div>
    <div class="slot" style="left:18px;top:169px;width:58px">10 AM</div>
    <div class="slot" style="left:89px;top:169px;width:59px">11 AM</div>
    <div class="abs" style="left:16px;top:226px;font-size:8.5px;text-decoration:underline">SHOW CALENDAR</div>
    <div class="btn" style="left:17px;top:268px;width:209px">TERMIN BUCHEN</div>
  </div>
  <div class="btn disabled" style="top:436px">JETZT ONLINE BESTPREIS BUCHEN</div>
</section>

<!-- Screen: Warenkorb -->
<section class="screen" style="left:718px;top:618px">
  <div class="statusbar"><span>●●●●● Netz</span><span class="clock">9:41 AM</span><span>100%<i class="batt"></i></span></div>
  <div class="appbar">
    <svg class="back" width="10" height="16" viewBox="0 0 10 16"><path d="M8 1L2 8l6 7" fill="none" stroke="#222" stroke-width="1.8"/></svg>
    <div class="brand"><i class="dot"></i>Flickwerkzentrale</div>
    <svg class="basket" width="20" height="17" viewBox="0 0 20 17"><path d="M2 7h14l-2 8H4z M5 7l4-5 4 5" fill="none" stroke="#222" stroke-width="1.5"/><text x="15" y="5" font-size="7" font-family="Roboto,sans-serif">3</text></svg>
  </div>
  <div class="title" style="top:81px">Warenkorb</div>
  <div class="abs" style="left:0;top:125px;width:100%;height:12px;background:#cdcdcd;font-size:7px;color:#e8e8e8;display:flex;justify-content:space-between;padding:0 28px 0 32px;align-items:center"><span>Leistung</span><span>Preis</span></div>
  <div class="line-item" style="top:137px;padding-left:32px"><span class="x">✕</span>Bluetooth Antenne<span class="old">200€ -50%</span><span class="price">100 €</span></div>
  <div class="line-item" style="top:170px;padding-left:32px"><span class="x">✕</span>SIM Lesemodul<span class="price solo">100 €</span></div>
  <div class="total" style="top:203px"><span>Total</span><span>200 €</span></div>
  <div class="btn" style="top:258px">ZUR KASSE</div>
  <div class="label" style="top:324px">Passende Leistungen</div>
  <div class="suggest" style="top:337px"><span class="ic">✱</span>Bluetooth Antenne<span class="info">i</span></div>
  <div class="suggest" style="top:370px"><span class="ic">●</span>W-LAN Antenne<span class="info">i</span></div>
  <div class="suggest" style="top:404px"><span class="ic">◠</span>GPS Antenne<span class="info">i</span></div>
  <div class="suggest" style="top:437px"><span class="ic">✎</span>SIM Lesemodul<span class="info">i</span></div>
</section>

<!-- Screen: Danke -->
<section class="screen" style="left:1047px;top:618px">
  <div class="statusbar"><span>●●●●● Netz</span><span class="clock">9:41 AM</span><span>100%<i class="batt"></i></span></div>
  <div class="appbar">
    <svg class="back" width="10" height="16" viewBox="0 0 10 16"><path d="M8 1L2 8l6 7" fill="none" stroke="#222" stroke-width="1.8"/></svg>
    <div class="brand"><i class="dot"></i>Flickwerkzentrale</div>
    <svg class="basket" width="20" height="17" viewBox="0 0 20 17"><path d="M2 7h14l-2 8H4z M5 7l4-5 4 5" fill="none" stroke="#222" stroke-width="1.5"/><text x="15" y="5" font-size="7" font-family="Roboto,sans-serif">3</text></svg>
  </div>
  <div class="title" style="top:81px">Vielen Dank!</div>
  <div class="center-text" style="top:140px;font-size:9.5px;font-weight:700;color:var(--green)">Fonwerk.de</div>
  <div class="center-text" style="top:169px">Ahornweg 6<br>89350 Talheim</div>
  <div class="center-text" style="top:209px">Öffnungszeiten:<br>Mo-Fr. 9.00 Uhr - 18.00 Uhr<br>Sa. 10.00 Uhr - 15.00 Uhr</div>
  <div class="abs" style="left:35px;top:288px;font-size:9.5px">Zahlungsmethoden:</div>
  <div class="paybox" style="left:142px;width:44px">Kartenpay</div>
  <div class="paybox" style="left:189px;width:57px">Zahlfix</div>
  <div class="line-item" style="top:320px;padding-left:35px">Bluetooth Antenne<span class="old">200€ -50%</span><span class="price">100 €</span></div>
  <div class="line-item" style="top:353px;padding-left:35px">SIM Lesemodul<span class="price solo">100 €</span></div>
  <div class="total" style="top:388px"><span>Total</span><span>200 €</span></div>
  <div class="btn" style="top:436px">BEZAHLEN</div>
</section>

</div>
</body>
</html>
```